Web Design

We need a website for a company based in Doha Qatar called
Lumara Maid Service.

It is the number one maid cleaning service company, and we have branches all over qatar.

Luxury Cleaning Service Provider.

The color scheme is gold, yellow and black like the logo.

Before they get to the website, there is an intro video.

The website should depict luxury.

Target Market(s)

People who need maids at their houses.

Industry/Entity Type

Cleaning Service

Requirements
Must have
• Luxury, Sleek, Modern

The opening sequence is a video which I already have. Its too big to upload here so I am going to put it on youtube.

After the opening sequence, the home page should have a widescreen photo background and it should change every five seconds, the first background photo should be of qatar westbay skyline. Then the second background should be of maid photos in cleaning positions. Then the third background should be of cleaner photos etc.

We will send you all the tabs and all the content later.

```html
<!DOCTYPE html>
<html lang="en">
<head>
<meta charset="utf-8">
<title>Lumara Maid Service – Contact Us</title>
<link href="https://fonts.googleapis.com/css2?family=Mulish:wght@400;600;700;800&family=Oswald:wght@500&display=swap" rel="stylesheet">
<style>
  :root {
    --gold: #e9b623;
    --gold-light: #f7d66a;
    --gold-deep: #d49e0b;
    --heading-gold: #d09a10;
    --nav-text: #4a2a05;
    --brown-dark: #2a1203;
    --footer-bg: #1f0e05;
    --ink: #333333;
    --muted: #8a8a8a;
    --field: #f5f5f5;
    --white: #ffffff;
  }
  * { box-sizing: border-box; margin: 0; padding: 0; }
  html, body { width: 968px; height: 1200px; overflow: hidden; }
  body { position: relative; background: var(--white); font-family: "Mulish", sans-serif; color: var(--ink); }

  .hero { position: absolute; left: 0; top: 0; width: 968px; height: 532px;
    background: linear-gradient(180deg, #9a9a9a 0%, #c8c8c8 40%, #8e8e8e 75%, #5e5e5e 100%); }
  .hero-topline { position: absolute; left: 0; top: 0; width: 968px; height: 5px; background: #4a2a05; }

  .nav-bar { position: absolute; left: 96px; top: 5px; width: 776px; height: 89px;
    background: linear-gradient(180deg, var(--gold-light) 0%, var(--gold) 100%);
    box-shadow: 0 6px 12px rgba(0,0,0,.35); }
  .nav-link { position: absolute; top: 45px; font-size: 11.5px; font-weight: 800;
    color: var(--nav-text); letter-spacing: .2px; white-space: nowrap; }

  .brand { position: absolute; left: 399px; top: 0; width: 170px; height: 136px;
    background: linear-gradient(180deg, #4a2a06 0%, #1a0b02 60%, #000 100%);
    display: flex; align-items: center; justify-content: center; flex-direction: column; }
  .brand-name { font-size: 13px; font-weight: 700; color: var(--gold-light); text-align: center; line-height: 1.3; }
  .brand-dot { width: 10px; height: 10px; border-radius: 50%; background: var(--gold-light); margin-bottom: 8px; }

  .slide { position: absolute; left: 96px; top: 108px; width: 776px; height: 376px;
    background: linear-gradient(110deg, #d9d9d9 0%, #9c9c9c 35%, #1f2d5a 62%, #2a2a2a 85%, #cfd7c9 100%); }
  .slide-dots { position: absolute; top: 455px; left: 450px; display: flex; gap: 5px; }
  .slide-dots span { width: 13px; height: 13px; border-radius: 50%; background: var(--white); border: 2px solid var(--gold); }
  .slide-dots span.active { background: #000; }

  .section-title { position: absolute; left: 97px; top: 583px; font-size: 14.5px; font-weight: 800; color: var(--heading-gold); }

  .contact-card { position: absolute; left: 97px; top: 629px; width: 308px; height: 446px;
    background: var(--white); border: 1px solid #e6e6e6; border-radius: 8px; box-shadow: 0 2px 3px rgba(0,0,0,.12); }
  .card-notch { position: absolute; left: 120px; top: 609px; }
  .field-label { position: absolute; left: 20px; font-size: 9.5px; color: var(--muted); }
  .field { position: absolute; left: 20px; width: 267px; background: var(--field); border-radius: 7px; }
  .field svg { position: absolute; right: 10px; top: 10px; }
  .submit { position: absolute; left: 21px; top: 389px; width: 72px; height: 29px; border-radius: 6px;
    background: var(--gold-deep); color: var(--white); font-family: "Oswald", sans-serif; font-size: 12px;
    display: flex; align-items: center; justify-content: center; gap: 4px; }

  .map { position: absolute; left: 459px; top: 631px; width: 413px; height: 159px;
    background: linear-gradient(135deg, #e8e4d8 0%, #d9d3c6 45%, #c9dcb4 70%, #ece6d4 100%); border: 1px solid #cfcfcf; }
  .info { position: absolute; left: 459px; font-size: 10.5px; color: var(--ink); white-space: nowrap; }
  .info b { font-weight: 700; }
  .info-head { position: absolute; left: 459px; font-size: 11px; font-weight: 700; color: var(--heading-gold); }

  .footer { position: absolute; left: 0; top: 1112px; width: 968px; height: 88px; background: var(--footer-bg); }
  .footer-links { position: absolute; left: 105px; top: 26px; display: flex; font-size: 11px; font-weight: 600; color: var(--white); }
  .footer-links span.sep { margin: 0 13px; }
  .copyright { position: absolute; left: 105px; top: 54px; font-size: 11px; font-weight: 600; color: var(--white); }
  .social { position: absolute; left: 845px; top: 33px; width: 22px; height: 22px; border-radius: 50%; border: 1.5px solid #cfc7bf; }
</style>
</head>
<body>
  <div class="hero" role="img" aria-label="City skyline by the water in grey tones"></div>
  <div class="hero-topline"></div>

  <nav class="nav-bar">
    <span class="nav-link" style="left:35px">HOME</span>
    <span class="nav-link" style="left:94px">ABOUT US</span>
    <span class="nav-link" style="left:174px">SERVICES</span>
    <span class="nav-link" style="left:251px">TEAM</span>
    <span class="nav-link" style="left:485px">LOCATIONS</span>
    <span class="nav-link" style="left:574px">TESTIMONIALS</span>
    <span class="nav-link" style="left:679px">CONTACT US</span>
  </nav>

  <div class="brand">
    <div class="brand-dot"></div>
    <div class="brand-name">Lumara Maid<br>Service</div>
  </div>

  <div class="slide" role="img" aria-label="Smiling receptionist on the phone at an office desk"></div>
  <div class="slide-dots"><span class="active"></span><span></span><span></span><span></span></div>

  <h2 class="section-title">CONTACT US</h2>

  <svg class="card-notch" width="32" height="22" viewBox="0 0 32 22">
    <path d="M0 21 L16 1 L32 21" fill="#fff" stroke="#e6e6e6" stroke-width="1"/>
  </svg>
  <form class="contact-card">
    <span class="field-label" style="top:24px">Your Name *</span>
    <div class="field" style="top:40px;height:32px">
      <svg width="14" height="14" viewBox="0 0 14 14"><circle cx="7" cy="4" r="3.2" fill="#777"/><path d="M1 14 C1 8 13 8 13 14Z" fill="#777"/></svg>
    </div>
    <span class="field-label" style="top:89px">Your email address *</span>
    <div class="field" style="top:105px;height:32px">
      <svg width="14" height="14" viewBox="0 0 14 14"><text x="0" y="12" font-size="13" fill="#777" font-family="Mulish, sans-serif">@</text></svg>
    </div>
    <span class="field-label" style="top:174px">Subject *</span>
    <div class="field" style="top:192px;height:32px"></div>
    <span class="field-label" style="top:242px">Your message</span>
    <div class="field" style="top:258px;height:112px">
      <svg width="14" height="11" viewBox="0 0 14 11"><rect x=".5" y=".5" width="13" height="10" fill="#888"/><path d="M.5 .5 L7 6 L13.5 .5" fill="none" stroke="#eee" stroke-width="1"/></svg>
    </div>
    <div class="submit">
      <svg width="6" height="9" viewBox="0 0 6 9"><path d="M1 1 L5 4.5 L1 8" fill="none" stroke="#fff" stroke-width="1.6"/></svg>SUBMIT
    </div>
  </form>

  <div class="map" role="img" aria-label="Street map showing the office location"></div>

  <p class="info" style="top:812px"><b>Email :</b> info@lumaramaidservice.com</p>
  <h3 class="info-head" style="top:859px">HEAD OFFICE</h3>
  <p class="info" style="top:883px"><b>Operations Manager:</b> Mr. Arun - +974 3000 1201</p>
  <p class="info" style="top:906px"><b>Complaints Manager :</b> Ms. Lina - +974 3000 1202</p>
  <h3 class="info-head" style="top:955px">OPERATIONS</h3>
  <p class="info" style="top:979px"><b>Cleaning Supervisor:</b> Ms. Noor - +974 7000 1203</p>
  <p class="info" style="top:1002px"><b>Transportation Supervisor:</b> Mr. Ravi - +974 3000 1204</p>

  <footer class="footer">
    <div class="footer-links">
      <span>Home</span><span class="sep">|</span><span>About Us</span><span class="sep">|</span><span>Services</span><span class="sep">|</span><span>Jobs</span><span class="sep">|</span><span>Maids</span><span class="sep">|</span><span>FAQ's</span><span class="sep">|</span><span>Testimonials</span><span class="sep">|</span><span>Contact Us</span>
    </div>
    <p class="copyright">© 2014 Company Name ,All  Rights Reserved</p>
    <div class="social"></div>
  </footer>
</body>
</html>
```